Sunset Harbor Living Web Page

We need a web page design that has two intro pages - first being a 'home page', then a link to the second page that has the 'content tabs' and a 'call to action' (see below).

The business helps people that wish to retire to S.E.Asia (Thailand, Malaysia, Indonesia,The Philippines etc) - to enjoy the lifestyle and the remaining years of their lives. What attracts S.E.Asia to many people is the lower cost, the atmoshpere and beauty of the tropics and the vibrancy of the various countries.

People that are wishing to make the most of their retirement and are adventurous at a great bargain compared to the cost of their own countries will be interested.

We help them achieve this - visa, financials (tax, gov't payments etc), introduce them to the right people for property, clubs, retirement facilities, insurance and so forth.

Therefore we are providing an extremely wide ranging service and this site will provide broad but general information only - with a call to action to come and see us for more specific information and how we can help them specifically.

This site will be predominantly for travel and lifestyle, it will be linked with another financial services (financial planning) site later down the track.

The colour scheme is dark green and blue - as per the attached logo design. Photos and background just think lifestyle and S.E.Asia - beaches/mountains/water/recreational activities for retirees.

Target market is mostly those coming up to retirement to those that are already retired. But we also expect to have some interest with younger people that would like to find out more and plan for the future. So a broad age group but I would say mostly 40-70 yrs old.

On the first (Home) page we would like our company name 'Sunset Harbor Living', our logo (which will be on all pages) and a statement such as: “Imagine a retirement where your dreams are brought to life, and you have never felt more alive. Let us show you how”. Then a link to the second page.

We would like an uncluttered site. On the second (contents) page the tabs would be:

- Visa
- Property
- Financials
- Travel
- Insurance & Healthcare
- Medical Tourism
- Cost of living
- Weekly Blogs and articles
- Sunset Harbor Living story

We would also like a call to action on the second page - asking them to leave their contact details if they wish to learn more or sign up to our weekly newsletter/blog.

We are open to suggestions and your imaginations.

Thank you
Malcolm

Font styles to use
Serif
Script

Colors
0255a3
3377b5
00a990
9bcb3c
abd036
33b8a4
85abd2
cadf82
86cfc6

Requirements
Must have
• I have been asked by the web designer to receive a 'Web Font' so that we can 'get off of Zentrofy'. Hope that makes sense.

```html
<!DOCTYPE html>
<html lang="en">
<head>
<meta charset="utf-8">
<title>Sunset Harbor Living</title>
<link rel="stylesheet" href="https://fonts.googleapis.com/css2?family=Cinzel:wght@700&family=Lato:ital,wght@0,400;0,700;1,400&family=Roboto:wght@400;500;700&family=Ubuntu:wght@500&display=swap">
<style>
:root{
  --blue:#1b9cd8;
  --blue-dark:#0e7fbf;
  --green:#1fa84a;
  --green-dark:#138a38;
  --headline-green:#1d9e3c;
  --ink:#222;
  --grey:#5b5b5b;
  --text:#555;
  --light:#f3f3f3;
  --header:#1c1c1c;
  --footer:#161616;
  --white:#fff;
}
*{margin:0;padding:0;box-sizing:border-box}
html,body{width:1200px;height:2711px;overflow:hidden}
body{position:relative;font-family:"Lato",sans-serif;color:var(--text);background:var(--white)}
.abs{position:absolute}

/* header */
.site-header{left:0;top:0;width:1200px;height:100px;background:linear-gradient(#2a2a2a,var(--header))}
.brand{left:85px;top:22px;display:flex;align-items:center;gap:14px}
.brand-dot{width:56px;height:56px;border-radius:50%;background:var(--green)}
.brand-name{font-family:"Roboto",sans-serif;font-weight:700;font-size:31px;color:var(--white)}
.main-nav a{position:absolute;top:61px;font-family:"Roboto",sans-serif;font-weight:700;font-size:14.5px;color:var(--white);text-decoration:none;letter-spacing:.2px}
.nav-active{left:580px;top:92px;width:42px;height:6px;background:var(--green)}
.social{display:flex;gap:14px}
.social span{width:28px;height:28px;border-radius:50%;border:2px solid var(--white)}

/* hero */
.hero{left:0;top:100px;width:1200px;height:583px;background:linear-gradient(180deg,#8fb4d2 0%,#c9a66a 22%,#3f6e3a 40%,#d8d2c0 58%,#4aa6b6 70%,#1c5c7a 100%)}
.hero-arrow{top:240px}
.hero-title{left:0;top:270px;width:1200px;text-align:center;font-family:"Cinzel",serif;font-weight:700;font-size:34px;line-height:40px;color:var(--headline-green);text-shadow:0 0 3px #02250c,1px 1px 2px #02250c}
.hero-cta{left:434px;top:446px;width:332px;height:54px;border:2px solid var(--white);border-radius:4px;background:var(--blue);display:flex;align-items:center;padding-left:12px;font-family:"Ubuntu",sans-serif;font-weight:500;font-size:25px;color:var(--white)}
.hero-cta .chev{position:absolute;right:0;top:-2px;width:54px;height:54px;border-radius:50%;background:var(--green);border:2px solid var(--white);display:flex;align-items:center;justify-content:center}

/* section titles */
.section-title{left:0;width:1200px;text-align:center;font-family:"Roboto",sans-serif;font-weight:500;font-size:38px}
.divider{left:330px;width:540px;height:14px}

/* welcome */
.welcome{left:0;top:683px;width:1200px;height:344px;background:var(--light)}
.welcome-title{top:52px;color:var(--grey)}
.welcome-title b{color:var(--blue);font-weight:500}
.welcome-text{left:121px;top:136px;width:958px;text-align:center;font-size:13.5px;line-height:23.5px;color:#444}
.btn{display:flex;align-items:center;justify-content:center;font-family:"Roboto",sans-serif;font-weight:700;color:var(--white);border-radius:3px}
.btn-more{left:526px;top:255px;width:146px;height:38px;background:var(--blue);font-size:15px;justify-content:flex-start;padding-left:12px}
.btn-more .chev{position:absolute;right:0;top:0;width:38px;height:38px;border-radius:50%;background:var(--green);border:2px solid var(--white);display:flex;align-items:center;justify-content:center}

/* services */
.services{left:0;top:1027px;width:1200px;height:451px;background:var(--blue)}
.services-title{top:40px;color:var(--white)}
.service-card{top:139px;width:239px;height:159px;border:4px solid var(--white);box-shadow:0 2px 6px rgba(0,0,0,.3)}
.service-label{top:314px;width:239px;text-align:center;font-family:"Roboto",sans-serif;font-size:20px;font-weight:500;color:var(--white)}
.btn-all{left:492px;top:370px;width:215px;height:38px;background:var(--green);font-size:15px;letter-spacing:.3px}

/* news & testimonials */
.col-title{font-family:"Roboto",sans-serif;font-size:36px;color:var(--grey);font-weight:500}
.col-title b{color:var(--ink);font-weight:500}
.col-rule{height:2px;background:#e2e2e2}
.pager{display:flex;gap:8px}
.news-thumb{left:81px;width:102px;height:100px;border:3px solid #fff;box-shadow:0 1px 4px rgba(0,0,0,.35)}
.news-item{left:204px;width:366px}
.news-item h3{font-family:"Lato",sans-serif;font-weight:700;font-size:15px;color:var(--ink);margin-bottom:6px}
.news-item .date{font-style:italic;font-size:11px;color:#777;margin-bottom:5px}
.news-item p{font-size:12.5px;line-height:18px;color:#555}
.news-item .more{display:block;margin-top:4px;font-size:10.5px;font-weight:700;color:var(--green)}
.col-divider{left:610px;top:1527px;width:2px;height:353px;background:#d8d8d8}
.avatar{left:652px;top:1603px;width:95px;height:95px;border-radius:50%;border:4px solid var(--blue);background:radial-gradient(circle at 50% 40%,#d9c0a8,#7a8fa6)}
.client-name{left:761px;top:1630px;font-family:"Roboto",sans-serif;font-weight:700;font-size:16px;color:var(--ink)}
.client-role{left:761px;top:1654px;font-size:13px;font-weight:700;color:var(--green)}
.quote{left:652px;top:1712px;width:465px;font-style:italic;font-size:12.5px;line-height:19.5px;color:#555}
.quote .mark{font-family:"Cinzel",serif;font-style:normal;font-weight:700;font-size:26px;color:#333;line-height:10px;vertical-align:-6px}

/* contact */
.contact{left:0;top:1930px;width:1200px;height:520px;background:linear-gradient(180deg,#2d3a3e 0%,#3f5a63 35%,#5e7b86 55%,#3a4d4f 80%,#2a3232 100%)}
.contact-title{top:52px;color:var(--white)}
.field{height:40px;background:var(--white);border:1px solid #ddd;font-size:12px;color:#777;padding:0 11px;display:flex;align-items:center}
.btn-submit{left:535px;top:2206px;width:130px;height:38px;background:var(--blue);font-size:15px;justify-content:flex-start;padding-left:22px}
.btn-submit .chev{position:absolute;right:0;top:0;width:38px;height:38px;border-radius:50%;background:var(--green);border:2px solid var(--white);display:flex;align-items:center;justify-content:center}

/* footer */
.footer{left:0;top:2380px;width:1200px;height:280px;background:var(--footer)}
.wave{left:0;top:2236px;width:1200px;height:190px}
.map{left:81px;top:2430px;width:262px;height:185px;border:3px solid #fff;background:linear-gradient(135deg,#cfe3c4,#e8e4d8 45%,#b7d3e6)}
.f-company{left:367px;top:2430px;width:200px}
.f-company h4{font-family:"Roboto",sans-serif;font-weight:700;font-size:12.5px;color:var(--white);margin-bottom:6px}
.f-company p{font-size:12px;line-height:21px;color:#aaa}
.f-contact{left:367px;display:flex;align-items:center;gap:12px}
.f-contact small{display:block;font-size:10px;color:#aaa}
.f-contact strong{display:block;font-size:13px;font-weight:400;color:var(--white)}
.f-icon{width:24px;height:24px;border-radius:50%;border:2px solid var(--green);display:flex;align-items:center;justify-content:center}
.newsletter{left:598px;top:2458px}
.newsletter h4{font-family:"Roboto",sans-serif;font-weight:700;font-size:18px;color:var(--white);display:flex;gap:10px;align-items:center}
.newsletter p{font-size:11.5px;color:#ccc;margin-top:10px}
.nl-input{left:598px;top:2526px;width:239px;height:36px;border:1px solid #555;background:#111;color:#ddd;font-size:12px;padding-left:11px;display:flex;align-items:center}
.btn-signup{left:598px;top:2580px;width:123px;height:37px;background:var(--green);font-size:15px}
.footer-brand{left:880px;top:2462px;width:240px;display:flex;flex-direction:column;align-items:center;gap:12px}
.footer-brand .brand-dot{width:80px;height:80px}
.footer-brand .brand-name{font-size:24px}
.bottom-bar{left:0;top:2660px;width:1200px;height:51px;background:var(--green);display:flex;align-items:center;justify-content:space-between;padding:0 98px 0 81px}
.bottom-bar p{font-size:12px;font-weight:700;color:var(--white)}
</style>
</head>
<body>

<header class="site-header abs">
  <div class="brand abs"><span class="brand-dot"></span><span class="brand-name">Sunset Harbor Living</span></div>
  <nav class="main-nav">
    <a style="left:580px">HOME</a>
    <a style="left:656px">SERVICES</a>
    <a style="left:755px">BLOG &amp; ARTICLES</a>
    <a style="left:909px">OUR STORY</a>
    <a style="left:1023px">CONTACT US</a>
  </nav>
  <div class="nav-active abs"></div>
  <div class="social abs" style="left:975px;top:19px"><span></span><span></span><span></span><span></span></div>
</header>

<section class="hero abs" role="img" aria-label="Tropical beachfront resort with palm trees and calm sea">
  <svg class="hero-arrow abs" style="left:40px" width="40" height="80" viewBox="0 0 40 80"><polyline points="36,4 6,40 36,76" fill="none" stroke="#fff" stroke-width="3"/></svg>
  <svg class="hero-arrow abs" style="left:1120px" width="40" height="80" viewBox="0 0 40 80"><polyline points="4,4 34,40 4,76" fill="none" stroke="#fff" stroke-width="3"/></svg>
  <h1 class="hero-title abs">Imagine A Retirement Where Your Dreams Are<br>Brought To Life,<br>&amp; You Have Never Felt More Alive</h1>
  <a class="hero-cta abs">Let Us Show You How<span class="chev"><svg width="26" height="22" viewBox="0 0 26 22"><polyline points="3,3 11,11 3,19" fill="none" stroke="#fff" stroke-width="2.5"/><polyline points="13,3 21,11 13,19" fill="none" stroke="#fff" stroke-width="2.5"/></svg></span></a>
</section>

<section class="welcome abs">
  <h2 class="section-title welcome-title abs">Welcome To <b>Sunset Harbor Living</b></h2>
  <svg class="divider abs" style="top:103px" viewBox="0 0 540 14"><line x1="0" y1="7" x2="250" y2="7" stroke="#ccc"/><line x1="290" y1="7" x2="540" y2="7" stroke="#ccc"/><circle cx="270" cy="7" r="6" fill="var(--green)"/></svg>
  <p class="welcome-text abs">Lorem ipsum dolor sit amet, consectetuer adipiscing elit, sed diam nonummy nibh euismod tincidunt ut laoreet dolore magna aliquam erat volutpat. Ut wisi enim ad minim veniam, quis nostrud exerci tation ullamcorper suscipit lobortis nisl ut aliquip ex ea commodo consequat. Duis autem vel eum iriure dolor in hendrerit in vulputate velit esse molestie consequat, vel illum dolore eu feugiat nulla facilisis at vero eros et accumsan et iusto odio dignissim qui blandit praesent luptatum zzril delenit augue duis dolore te feugait nulla facilisi.</p>
  <a class="btn btn-more abs">READ MORE<span class="chev"><svg width="18" height="14" viewBox="0 0 18 14"><polyline points="2,2 7,7 2,12" fill="none" stroke="#fff" stroke-width="2"/><polyline points="9,2 14,7 9,12" fill="none" stroke="#fff" stroke-width="2"/></svg></span></a>
</section>

<section class="services abs">
  <h2 class="section-title services-title abs">Our Services</h2>
  <svg class="divider abs" style="top:91px" viewBox="0 0 540 14"><line x1="0" y1="7" x2="250" y2="7" stroke="#6cc3ea"/><line x1="290" y1="7" x2="540" y2="7" stroke="#6cc3ea"/><circle cx="270" cy="7" r="6" fill="#6cc3ea"/></svg>
  <svg class="abs" style="left:38px;top:204px" width="18" height="34" viewBox="0 0 18 34"><polyline points="16,2 3,17 16,32" fill="none" stroke="#fff" stroke-width="2.5"/></svg>
  <svg class="abs" style="left:1145px;top:204px" width="18" height="34" viewBox="0 0 18 34"><polyline points="2,2 15,17 2,32" fill="none" stroke="#fff" stroke-width="2.5"/></svg>
  <div class="service-card abs" style="left:81px;background:linear-gradient(135deg,#c9a57a,#2b4d8a 60%,#b08a5e)" role="img" aria-label="Passport with visa stamps"></div>
  <div class="service-card abs" style="left:347px;background:linear-gradient(135deg,#5c8a2e,#e6e2d8 55%,#3f6b24)" role="img" aria-label="Hand holding a small model house"></div>
  <div class="service-card abs" style="left:614px;background:linear-gradient(135deg,#dfe7ef,#5a7ea4 60%,#cfd9e4)" role="img" aria-label="Financial papers with a calculator and pen"></div>
  <div class="service-card abs" style="left:880px;background:linear-gradient(180deg,#6d8fb8,#e9eef4 55%,#b9c4cf)" role="img" aria-label="Hiker resting on snowy mountains"></div>
  <div class="service-label abs" style="left:81px">VISA</div>
  <div class="service-label abs" style="left:347px">PROPERTY</div>
  <div class="service-label abs" style="left:614px">FINANCIALS</div>
  <div class="service-label abs" style="left:880px">TRAVEL</div>
  <a class="btn btn-all abs">VIEW ALL SERVICE</a>
</section>

<section class="news">
  <h2 class="col-title abs" style="left:81px;top:1524px">Latest <b>News</b></h2>
  <div class="pager abs" style="left:528px;top:1540px"><svg width="14" height="24" viewBox="0 0 14 24"><polyline points="12,2 3,12 12,22" fill="none" stroke="#bbb" stroke-width="2"/></svg><svg width="14" height="24" viewBox="0 0 14 24"><polyline points="2,2 11,12 2,22" fill="none" stroke="#222" stroke-width="2"/></svg></div>
  <div class="col-rule abs" style="left:81px;top:1580px;width:489px"></div>

  <div class="news-thumb abs" style="top:1621px;background:linear-gradient(180deg,#4a8fc8,#7fc3a8 50%,#e8dcc0)" role="img" aria-label="Tropical beach with palm tree"></div>
  <article class="news-item abs" style="top:1622px">
    <h3>Ut tellus dolor, dapibus smit dollar nomk egemop</h3>
    <div class="date">Posted On 01.01.2015</div>
    <p>Duis autem vel eum iriure dolor in hendrerit in at vero erosacc sa iusto odio dignissim quosli blandit praesent luptatum zzril dolore duis</p>
    <span class="more">READ MORE</span>
  </article>
  <div class="col-rule abs" style="left:204px;top:1746px;width:366px;height:1px"></div>
  <div class="news-thumb abs" style="top:1768px;background:linear-gradient(180deg,#e8c98a,#c98a4a 60%,#6b4a2e)" role="img" aria-label="Family walking together at sunset"></div>
  <article class="news-item abs" style="top:1769px">
    <h3>Ut tellus dolor, dapibus smit dollar nomk egemop</h3>
    <div class="date">Posted On 01.01.2015</div>
    <p>Duis autem vel eum iriure dolor in hendrerit in at vero erosacc sa iusto odio dignissim quosli blandit praesent luptatum zzril dolore duis</p>
    <span class="more">READ MORE</span>
  </article>
</section>

<div class="col-divider abs"></div>

<section class="testimonials">
  <h2 class="col-title abs" style="left:652px;top:1524px">Client <b>Testimonials</b></h2>
  <div class="pager abs" style="left:1082px;top:1540px"><svg width="14" height="24" viewBox="0 0 14 24"><polyline points="12,2 3,12 12,22" fill="none" stroke="#bbb" stroke-width="2"/></svg><svg width="14" height="24" viewBox="0 0 14 24"><polyline points="2,2 11,12 2,22" fill="none" stroke="#222" stroke-width="2"/></svg></div>
  <div class="col-rule abs" style="left:652px;top:1580px;width:467px"></div>
  <div class="avatar abs" role="img" aria-label="Client portrait"></div>
  <div class="client-name abs">MR. QUIS NOSTRUD EXERCI</div>
  <div class="client-role abs">Business Man</div>
  <p class="quote abs"><span class="mark">“</span> Utm tellus dolor, dapibus eget, elemen velmki cursus eleifelita arnanokmn auctorbni wisi et urnam. Lorem ipsum dolor sit amet, conse ctetur adipisc ngop elit. Nulla in sollic itudin velit, bibendum velit. Cras vel facilisis ipsum, et venenat risus. Duis autem vel eum iriure dolor in hendrerit in at vero erosacc sa iustoml odio dignissim quosliin sollic itudin <span class="mark">”</span></p>
</section>

<section class="contact abs" role="img" aria-label="Palm-framed tropical sea at dusk">
  <h2 class="section-title contact-title abs">Get In Touch</h2>
  <svg class="divider abs" style="top:105px" viewBox="0 0 540 14"><line x1="0" y1="7" x2="250" y2="7" stroke="#8a9a9c"/><line x1="290" y1="7" x2="540" y2="7" stroke="#8a9a9c"/><circle cx="270" cy="7" r="6" fill="#8a9a9c"/></svg>
</section>
<form>
  <div class="field abs" style="left:210px;top:2089px;width:247px">Enter Your Name</div>
  <div class="field abs" style="left:475px;top:2089px;width:248px">Enter Your Email Address</div>
  <div class="field abs" style="left:743px;top:2089px;width:247px">Enter Your Phone Number</div>
  <div class="field abs" style="left:210px;top:2148px;width:247px">Enter Your Location</div>
  <div class="field abs" style="left:475px;top:2148px;width:515px">Enter Your Comments</div>
  <a class="btn btn-submit abs">SUBMIT<span class="chev"><svg width="18" height="14" viewBox="0 0 18 14"><polyline points="2,2 7,7 2,12" fill="none" stroke="#fff" stroke-width="2"/><polyline points="9,2 14,7 9,12" fill="none" stroke="#fff" stroke-width="2"/></svg></span></a>
</form>

<footer>
  <div class="footer abs"></div>
  <svg class="wave abs" viewBox="0 0 1200 190" preserveAspectRatio="none">
    <path d="M0,150 C250,40 520,210 820,120 C980,70 1100,30 1200,0 L1200,190 L0,190 Z" fill="var(--footer)"/>
    <path d="M0,150 C250,40 520,210 820,120 C980,70 1100,30 1200,0 L1200,40 C1100,70 980,110 820,150 C520,235 250,90 0,175 Z" fill="var(--blue)"/>
    <path d="M300,150 C500,210 700,190 900,120 C1000,90 1120,60 1200,50 L1200,60 C1110,75 1000,110 900,140 C700,205 500,215 300,150 Z" fill="var(--blue-dark)"/>
  </svg>
  <div class="map abs" role="img" aria-label="Street map showing the office location"></div>
  <div class="f-company abs">
    <h4>SUNSET HARBOR LIVING</h4>
    <p>Duis autem vel eum iriure dolor in hendrerit in at vero</p>
  </div>
  <div class="f-contact abs" style="top:2512px"><span class="f-icon"><svg width="12" height="12" viewBox="0 0 12 12"><path d="M2,1 L4.5,1 L5.5,3.5 L4,4.8 C4.8,6.5 5.8,7.5 7.2,8 L8.5,6.5 L11,7.5 L11,10 C6,11 1,6 2,1 Z" fill="var(--green)"/></svg></span><span><small>Call Us Today</small><strong>(555) 014-2290</strong></span></div>
  <div class="f-contact abs" style="top:2567px"><span class="f-icon"><svg width="12" height="10" viewBox="0 0 12 10"><rect x="1" y="1" width="10" height="8" fill="none" stroke="var(--green)" stroke-width="1.4"/><polyline points="1,1 6,6 11,1" fill="none" stroke="var(--green)" stroke-width="1.4"/></svg></span><span><small>Write To Us</small><strong>info@sunsetharborliving.com</strong></span></div>

  <div class="newsletter abs">
    <h4><svg width="30" height="18" viewBox="0 0 30 18"><polygon points="0,0 30,3 12,18 10,9" fill="var(--green)"/></svg>Newsletter Signup</h4>
    <p>Sign Up To Our Weekly Newsletter/ Blog!</p>
  </div>
  <div class="nl-input abs">Enter Your Email Here</div>
  <a class="btn btn-signup abs">SIGNUP</a>

  <div class="footer-brand abs"><span class="brand-dot"></span><span class="brand-name">Sunset Harbor Living</span></div>

  <div class="bottom-bar abs">
    <p>Copyright © 2016 Sunset Harbor Living &nbsp;|&nbsp; All Rights Reserved.</p>
    <div class="social"><span></span><span></span><span></span><span></span></div>
  </div>
</footer>

</body>
</html>
```